BrindleStaffing Business Card Design

We are a staffing company finding positions for dedicated nurses and physicians.

Target Market(s)

Business Professionals

Industry/Entity Type

Staffing

Contact Information for Business Card

Gordon Pratley
Chairman
417 39th Avenue South
SAINT PETERSBURG FL 33712
813-555-4172 Mobile
813-555-8036 Fax
gpratley@brindlestaffing.com
www.brindlestaffing.com

Font styles to use
Sans Serif

Colors
fbee3e
f04a50
f37122

Requirements
Must have
• Logo Attached, see colors below. We'd like to see Yellow, Orange and Red.

```html
<!DOCTYPE html>
<html lang="en">
<head>
<meta charset="utf-8">
<title>BrindleStaffing Business Card</title>
<link rel="stylesheet" href="https://fonts.googleapis.com/css2?family=Nunito:wght@600;800&family=Roboto:wght@400&display=swap">
<style>
  :root {
    --bg: #e9e6e1;
    --card: #ffffff;
    --orange: #f37122;
    --orange-light: #f68a45;
    --red: #f04a50;
    --yellow: #fbee3e;
    --dot-tint: #fdf1e4;
    --text-light: #ffffff;
    --text-dark: #4a4440;
  }
  * { box-sizing: border-box; margin: 0; padding: 0; }
  html, body { width: 1200px; height: 1040px; overflow: hidden; background: var(--bg); }
  .canvas { position: relative; width: 1200px; height: 1040px; }
  .card {
    position: absolute; width: 760px; height: 434px;
    background: var(--card); border-radius: 22px; overflow: hidden;
    box-shadow: 0 10px 28px rgba(0,0,0,0.18);
  }
  .card--front { left: 60px; top: 50px; }
  .card--back { left: 380px; top: 556px; }

  .front-waves { position: absolute; inset: 0; width: 100%; height: 100%; }

  .identity { position: absolute; left: 36px; top: 140px; }
  .brand-name {
    font-family: "Nunito", sans-serif; font-weight: 800; font-size: 36px;
    color: var(--red); letter-spacing: -0.5px; display: flex; align-items: center; gap: 10px;
    white-space: nowrap;
  }
  .brand-dot { width: 12px; height: 12px; border-radius: 50%; background: var(--orange); }
  .person-name {
    font-family: "Nunito", sans-serif; font-weight: 600; font-size: 28px;
    color: var(--red); margin-top: 20px; margin-left: 50px; white-space: nowrap;
  }
  .person-title {
    font-family: "Nunito", sans-serif; font-weight: 600; font-size: 17px;
    color: var(--orange); margin-left: 50px; margin-top: 2px;
  }

  .contact {
    position: absolute; right: 30px; top: 58px; list-style: none;
    font-family: "Roboto", sans-serif; font-size: 16px; color: var(--text-light);
    text-align: right; line-height: 30px;
  }
  .contact li { display: flex; justify-content: flex-end; align-items: center; gap: 10px; white-space: nowrap; }
  .contact svg { width: 16px; height: 16px; fill: none; stroke: var(--text-light); stroke-width: 1.8; }
  .address {
    position: absolute; right: 30px; bottom: 32px; white-space: nowrap;
    font-family: "Roboto", sans-serif; font-size: 16px; color: var(--text-light);
  }

  .back-tint {
    position: absolute; inset: 0;
    background: radial-gradient(circle at 50% 50%, #fffaf4 0%, var(--dot-tint) 100%);
  }
  .back-brand {
    position: absolute; left: 0; right: 0; top: 150px;
    display: flex; justify-content: center;
  }
  .back-brand .brand-name { font-size: 64px; }
  .back-brand .brand-dot { width: 16px; height: 16px; }
  .back-url {
    position: absolute; left: 0; right: 0; bottom: 100px; text-align: center;
    font-family: "Roboto", sans-serif; font-size: 16px; letter-spacing: 7px; color: var(--text-dark);
  }
</style>
</head>
<body>
<main class="canvas">

  <section class="card card--front" aria-label="Business card front">
    <svg class="front-waves" viewBox="0 0 760 434" preserveAspectRatio="none" aria-hidden="true">
      <path d="M190,434 C290,400 340,320 355,230 C370,130 410,40 520,0 L760,0 L760,434 Z" fill="#fbee3e"/>
      <path d="M218,434 C314,401 368,321 383,230 C398,130 438,40 548,0 L760,0 L760,434 Z" fill="#ffffff"/>
      <path d="M234,434 C330,402 384,322 399,230 C414,130 454,40 564,0 L760,0 L760,434 Z" fill="#f37122"/>
      <path d="M596,0 C520,34 484,90 468,150" fill="none" stroke="#ffffff" stroke-width="3" opacity="0.85"/>
      <path d="M618,0 C548,36 508,90 490,150" fill="none" stroke="#f04a50" stroke-width="9" opacity="0.45"/>
    </svg>

    <div class="identity">
      <div class="brand-name"><span class="brand-dot"></span>BrindleStaffing</div>
      <p class="person-name">Gordon Pratley</p>
      <p class="person-title">Chairman</p>
    </div>

    <ul class="contact">
      <li>813-555-4172
        <svg viewBox="0 0 16 16"><rect x="4" y="1.5" width="8" height="13" rx="1.5"/></svg></li>
      <li>813-555-8036
        <svg viewBox="0 0 16 16"><rect x="2" y="6" width="12" height="8" rx="1"/><path d="M4.5 6V2h7v4"/></svg></li>
      <li>gpratley@brindlestaffing.com
        <svg viewBox="0 0 16 16"><rect x="1.5" y="3.5" width="13" height="9" rx="1"/><path d="M1.5 4l6.5 5 6.5-5"/></svg></li>
      <li>www.brindlestaffing.com
        <svg viewBox="0 0 16 16"><circle cx="8" cy="8" r="6.5"/><path d="M1.5 8h13M8 1.5c-3 3-3 10 0 13M8 1.5c3 3 3 10 0 13"/></svg></li>
    </ul>
    <p class="address">417 39th Avenue South, Saint Petersburg FL 33712</p>
  </section>

  <section class="card card--back" aria-label="Business card back">
    <div class="back-tint" role="img" aria-label="Soft pale warm dotted background pattern"></div>
    <div class="back-brand">
      <div class="brand-name"><span class="brand-dot"></span>BrindleStaffing</div>
    </div>
    <p class="back-url">www.brindlestaffing.com</p>
  </section>

</main>
</body>
</html>
```